A revolutionary website for a revolutionary construction company

I am looking for inspirations... please help me and read the attached brief

I would like to achieve a website design that is modern, premium dynamic and drives emotions. I do not want a design that can be found on a normal template. Having that said, I would also like the utilisation of Illustrations that are relation to the company’s services…. Also would like to have illustrations dynamic when you navigate on them. So a young, dynamic and parallax design website that will show off these requirements. Also to add trust, with all pages designed.

please see attachements.
Updates

Low design quality

Target Market(s)

Please read brief

Number of Pages Required

5+ page

Font styles to use
Other font styles liked:
• Futura

Requirements
Must have
• Please read brief - colours to be matching logo colours
Nice to have
Should not have

```html
<!DOCTYPE html>
<html lang="en">
<head>
<meta charset="utf-8">
<title>Stoneleaf Designs</title>
<link href="https://fonts.googleapis.com/css2?family=Jost:wght@300;400;500;600;700&display=swap" rel="stylesheet">
<style>
:root{
  --crimson:#9e0b3d;
  --crimson-dark:#8a0934;
  --ink:#1f2a33;
  --muted:#6b6b6b;
  --tab-active:#5e5457;
  --light:#efefef;
  --white:#ffffff;
  --black:#000000;
}
*{margin:0;padding:0;box-sizing:border-box}
html,body{width:1200px;height:3185px;overflow:hidden;background:var(--white);font-family:'Jost',sans-serif;color:var(--ink)}
.page{position:relative;width:1200px;height:3185px;overflow:hidden}
.abs{position:absolute}

/* header */
.header{left:0;top:0;width:1200px;height:104px;background:var(--white);z-index:3}
.brand-disc{left:58px;top:-90px;width:302px;height:306px;border-radius:50%;background:var(--white);z-index:4}
.brand-mark{left:166px;top:17px;width:84px;height:84px;border-radius:50%;border:2px solid #555;z-index:5}
.brand-name{left:78px;top:112px;width:260px;text-align:center;font-size:14px;font-weight:500;letter-spacing:3px;color:var(--crimson);white-space:nowrap;line-height:18px;z-index:5}
.brand-tag{left:78px;top:132px;width:260px;text-align:center;font-size:11.5px;color:var(--crimson);white-space:nowrap;line-height:15px;z-index:5}
.nav{top:42px;left:414px;display:flex;gap:45px;font-size:16px;z-index:5}
.nav a{color:var(--ink);text-decoration:none}
.nav a.current{color:var(--crimson)}
.social-top{top:32px;left:894px;display:flex;gap:11px;z-index:5}
.social-top span{width:40px;height:40px;border-radius:50%;background:var(--crimson);box-shadow:0 1px 3px rgba(0,0,0,.3)}

/* hero */
.hero-photo{left:0;top:104px;width:771px;height:620px;background:linear-gradient(180deg,#8fb0d4 0%,#a9b7c2 30%,#6f7d8a 55%,#5b6a78 80%,#4c5a66 100%)}
.hero-photo-side{left:771px;top:104px;width:429px;height:620px;background:linear-gradient(160deg,#d98aa7 0%,#c9648a 60%,#d27ea0 100%)}
.hero-title{left:106px;top:318px;font-size:64px;font-weight:600;color:var(--white);text-shadow:0 2px 6px rgba(0,0,0,.45);white-space:nowrap}
.hero-text{left:108px;top:406px;font-size:13.5px;font-weight:600;line-height:24px;color:var(--white);text-shadow:0 1px 3px rgba(0,0,0,.6);white-space:nowrap}
.slider-btn{left:736px;top:374px;width:74px;height:74px}

/* about */
.eyebrow{font-size:17px;font-weight:500;letter-spacing:6px;color:var(--black)}
.section-title{font-size:43px;font-weight:600;color:var(--crimson);letter-spacing:.5px;white-space:nowrap}
.copy{font-size:14.5px;font-weight:300;line-height:25.7px;color:var(--muted);white-space:nowrap}
.about-eyebrow{left:110px;top:818px}
.about-title{left:108px;top:843px}
.about-copy{left:110px;top:910px}
.about-copy p+p{margin-top:25.7px}
.about-image{left:592px;top:824px;width:548px;height:364px;background:radial-gradient(ellipse at center,#e4e7ea 0%,#eef1f4 55%,#ffffff 100%)}

/* services */
.services-eyebrow{left:0;top:1259px;width:1200px;text-align:center}
.services-title{left:0;top:1284px;width:1200px;text-align:center}
.tabs{left:146px;top:1342px;height:56px;display:flex;font-size:17px;font-weight:500;color:#4a4446;white-space:nowrap}
.tab{height:56px;line-height:56px;padding:0 24px}
.tab.active{background:var(--tab-active);color:var(--white)}
.tab:nth-child(2){margin-left:14px}
.tab:nth-child(3){margin-left:10px}
.tab:nth-child(4){margin-left:16px}
.tab:nth-child(5){margin-left:10px}
.service-band{left:0;top:1398px;width:1200px;height:436px;background:var(--crimson)}
.service-image{left:111px;top:1467px;width:477px;height:287px;background:linear-gradient(135deg,#e2ded6 0%,#d6d1c7 60%,#cfc9be 100%)}
.service-copy{left:631px;top:1464px;color:var(--white)}
.service-copy p+p{margin-top:25.7px}

/* blog */
.blog-title{left:0;top:1900px;width:1200px;text-align:center}
.card{top:1980px;width:313px}
.card-image{width:313px;height:215px}
.card h3{margin-top:18px;text-align:center;font-size:22px;font-weight:500;color:var(--ink)}
.card .date{margin-top:2px;display:flex;justify-content:center;align-items:center;gap:4px;font-size:15px;font-weight:500;color:var(--crimson)}
.card .excerpt{margin-top:4px;text-align:center;font-size:14px;font-weight:300;line-height:24px;color:var(--muted);white-space:nowrap}
.c1{left:111px}.c2{left:444px}.c3{left:776px}
.c1 .card-image{background:linear-gradient(180deg,#3a3a3a 0%,#8c8478 45%,#b8b2aa 100%)}
.c2 .card-image{background:linear-gradient(180deg,#cfd3d6 0%,#eeeeee 50%,#c9c9c9 100%)}
.c3 .card-image{background:linear-gradient(180deg,#a9c2dc 0%,#b49a74 50%,#8a7458 100%)}

/* contact */
.contact{left:0;top:2428px;width:1200px;height:657px;background:var(--light)}
.contact-title{left:0;top:2500px;width:1200px;text-align:center}
.info{top:2581px;display:flex;align-items:center;gap:17px}
.info svg{flex:none}
.info div{font-size:14px;font-weight:300;line-height:24px;color:var(--muted);white-space:nowrap}
.i1{left:214px}.i2{left:514px}.i3{left:762px}
.field{background:var(--white);border:1px solid #d9d9d9;font-size:14px;color:#555;padding:18px 17px}
.f-name{left:216px;top:2672px;width:369px;height:55px}
.f-email{left:614px;top:2672px;width:369px;height:55px}
.f-phone{left:216px;top:2749px;width:766px;height:55px}
.f-msg{left:216px;top:2826px;width:766px;height:132px}
.submit{left:535px;top:2979px;width:129px;height:53px;background:var(--crimson);color:var(--white);font-size:14px;font-weight:700;text-align:center;line-height:53px}

/* footer */
.footer{left:0;top:3085px;width:1200px;height:100px;background:var(--black)}
.social-foot{left:110px;top:3114px;display:flex;gap:5px}
.social-foot span{width:40px;height:40px;border-radius:50%;border:2px solid var(--white)}
.copyright{left:741px;top:3122px;font-size:16px;color:var(--white);white-space:nowrap}
</style>
</head>
<body>
<div class="page">

  <div class="abs hero-photo" role="img" aria-label="Aerial photo of a city construction site with tower cranes"></div>
  <div class="abs hero-photo-side" role="img" aria-label="Pink-tinted photo of an interior under renovation"></div>
  <h1 class="abs hero-title">Stoneleaf Designs</h1>
  <p class="abs hero-text">Lorem ipsum dolor sit amet, consectetur adipiscing elit, sed do eiusmod<br>tempor incididunt ut labore et dolore magna aliqua. Ut enim ad minim<br>veniam, quis nostrud</p>
  <svg class="abs slider-btn" viewBox="0 0 74 74">
    <circle cx="37" cy="37" r="35" fill="none" stroke="#fff" stroke-width="2"/>
    <path d="M31 30 L25 37 L31 44" fill="none" stroke="#fff" stroke-width="2"/>
    <path d="M45 30 L51 37 L45 44" fill="none" stroke="#fff" stroke-width="2"/>
  </svg>

  <header class="abs header"></header>
  <div class="abs brand-disc"></div>
  <div class="abs brand-mark"></div>
  <div class="abs brand-name">Stoneleaf Designs</div>
  <div class="abs brand-tag">Building with peace of mind</div>
  <nav class="abs nav">
    <a class="current" href="#">Home</a><a href="#">About</a><a href="#">Services</a><a href="#">Blog</a><a href="#">Contact us</a>
  </nav>
  <div class="abs social-top"><span></span><span></span><span></span><span></span></div>

  <div class="abs eyebrow about-eyebrow">ABOUT US</div>
  <h2 class="abs section-title about-title">STONELEAF DESIGNS</h2>
  <div class="abs copy about-copy">
    <p>Lorem ipsum dolor sit amet, consectetur adipiscing elit, sed do eiusmod<br>tempor incididunt ut labore et dolore magna aliqua. Ut enim ad minim<br>veniam, quis nostrud exercitation ullamco laboris nisi ut aliquip ex ea<br>commodo consequat. Duis aute irure dolor in reprehenderit in voluptate<br>velit esse cillum dolore</p>
    <p>Lorem ipsum dolor sit amet, consectetur adipiscing elit, sed do eiusmod<br>tempor incididunt ut labore et dolore magna aliqua. Ut enim ad minim<br>veniam, quis nostrud exercitation ullamco laboris nisi ut aliquip ex ea<br>commodo consequat. Duis aute irure dolor in reprehenderit in voluptate<br>velit esse cillum dolore</p>
  </div>
  <div class="abs about-image" role="img" aria-label="Watercolour sketch of a modern bathroom interior"></div>

  <div class="abs eyebrow services-eyebrow">WHAT WE DO</div>
  <h2 class="abs section-title services-title">OUR SERVICES</h2>
  <div class="abs tabs">
    <div class="tab active">Lorem ipsum</div>
    <div class="tab">Dolor sit amet</div>
    <div class="tab">Consectetur adipiscing</div>
    <div class="tab">Eiusmod tempor</div>
    <div class="tab">Incididunt</div>
  </div>
  <section class="abs service-band"></section>
  <div class="abs service-image" role="img" aria-label="Isometric illustration of a furnished apartment floor plan"></div>
  <div class="abs copy service-copy">
    <p>Lorem ipsum dolor sit amet, consectetur adipiscing elit, sed do eiusmod<br>tempor incididunt ut labore et dolore magna aliqua. Ut enim ad minim<br>veniam, quis nostrud exercitation ullamco laboris nisi ut aliquip ex ea<br>commodo consequat. Duis aute irure dolor in reprehenderit in voluptate<br>velit esse cillum dolore</p>
    <p>Lorem ipsum dolor sit amet, consectetur adipiscing elit, sed do eiusmod<br>tempor incididunt ut labore et dolore magna aliqua. Ut enim ad minim<br>veniam, quis nostrud exercitation ullamco laboris nisi ut aliquip ex ea<br>commodo consequat. Duis aute irure dolor in reprehenderit in voluptate<br>velit esse cillum dolore</p>
  </div>

  <h2 class="abs section-title blog-title">LATEST BLOG</h2>
  <article class="abs card c1">
    <div class="card-image" role="img" aria-label="Photo of a modern meeting room"></div>
    <h3>Sed ut perspiciatis</h3>
    <div class="date"><svg width="14" height="14" viewBox="0 0 14 14"><rect x="1" y="2" width="12" height="11" fill="none" stroke="#9e0b3d" stroke-width="1.5"/><path d="M1 5h12M4 0v3M10 0v3" stroke="#9e0b3d" stroke-width="1.5"/></svg>Jan 21,2020</div>
    <p class="excerpt">Sed ut perspiciatis unde omnis iste<br>natus error sit voluptatem accusantium<br>doloremque laudantium</p>
  </article>
  <article class="abs card c2">
    <div class="card-image" role="img" aria-label="Photo of a bright empty office corridor"></div>
    <h3>Sed ut perspiciatis</h3>
    <div class="date"><svg width="14" height="14" viewBox="0 0 14 14"><rect x="1" y="2" width="12" height="11" fill="none" stroke="#9e0b3d" stroke-width="1.5"/><path d="M1 5h12M4 0v3M10 0v3" stroke="#9e0b3d" stroke-width="1.5"/></svg>Jan 21,2020</div>
    <p class="excerpt">Sed ut perspiciatis unde omnis iste<br>natus error sit voluptatem accusantium<br>doloremque laudantium</p>
  </article>
  <article class="abs card c3">
    <div class="card-image" role="img" aria-label="Photo of scaffolding on a building facade"></div>
    <h3>Sed ut perspiciatis</h3>
    <div class="date"><svg width="14" height="14" viewBox="0 0 14 14"><rect x="1" y="2" width="12" height="11" fill="none" stroke="#9e0b3d" stroke-width="1.5"/><path d="M1 5h12M4 0v3M10 0v3" stroke="#9e0b3d" stroke-width="1.5"/></svg>Jan 21,2020</div>
    <p class="excerpt">Sed ut perspiciatis unde omnis iste<br>natus error sit voluptatem accusantium<br>doloremque laudantium</p>
  </article>

  <section class="abs contact"></section>
  <h2 class="abs section-title contact-title">CONTACT US</h2>
  <div class="abs info i1">
    <svg width="64" height="64" viewBox="0 0 64 64"><circle cx="32" cy="32" r="30" fill="none" stroke="#9e0b3d" stroke-width="2.5"/><path d="M32 22a7 7 0 0 1 7 7c0 6-7 14-7 14s-7-8-7-14a7 7 0 0 1 7-7z" fill="#9e0b3d"/><circle cx="32" cy="29" r="2.6" fill="#efefef"/></svg>
    <div>123,Lorem ipsum dolor sit<br>amet, consectetur</div>
  </div>
  <div class="abs info i2">
    <svg width="64" height="64" viewBox="0 0 64 64"><circle cx="32" cy="32" r="30" fill="none" stroke="#9e0b3d" stroke-width="2.5"/><path d="M24 22l4-1 3 6-2.5 2c1.5 3 3.5 5 6.5 6.5l2-2.5 6 3-1 4c-9 1-19-9-18-18z" fill="#9e0b3d"/></svg>
    <div>Phone:<br>+1 888 888 8888</div>
  </div>
  <div class="abs info i3">
    <svg width="64" height="64" viewBox="0 0 64 64"><circle cx="32" cy="32" r="30" fill="none" stroke="#9e0b3d" stroke-width="2.5"/><rect x="21" y="24" width="22" height="16" rx="2" fill="#9e0b3d"/><path d="M21 26l11 8 11-8" fill="none" stroke="#efefef" stroke-width="1.8"/></svg>
    <div>Email address<br>info@companyname.com</div>
  </div>
  <div class="abs field f-name">Name</div>
  <div class="abs field f-email">Email address</div>
  <div class="abs field f-phone">Phone</div>
  <div class="abs field f-msg">Message</div>
  <div class="abs submit">SUBMIT</div>

  <footer class="abs footer"></footer>
  <div class="abs social-foot"><span></span><span></span><span></span><span></span></div>
  <div class="abs copyright">© 2020 Company Name | All Rights Reserved</div>

</div>
</body>
</html>
```